Kestrel Home Business Card Design

We need a business card for a Building company based in Queensland, Australia. Our colours are orange black and we do base all our homes design names and other aspect of our business on astrology. We want the consumer to perceive the company as professional and to attract investors to our company.We have over 20 years in the building industry.We pride ourselves on our innovation of designs and making the building process for anyone from families to investor a smooth and simple experience.
Business
Amelia Prichard0411752116PO Box 454, Mudgeerbaameliaprichard@zodiachomes.com

```html
<!DOCTYPE html>
<html lang="en">
<head>
<meta charset="utf-8">
<title>Kestrel Homes – Business Card</title>
<link href="https://fonts.googleapis.com/css2?family=Montserrat:wght@700;800&family=Open+Sans:wght@400;700&display=swap" rel="stylesheet">
<style>
  :root {
    --backdrop: #e4e4e4;
    --card-black: #0d0d0e;
    --card-black-soft: #1c1c1e;
    --brand-orange: #ec7a1c;
    --brand-orange-light: #f08d33;
    --text-white: #ffffff;
    --text-muted: #d9d9d9;
    --ghost-ring: rgba(255,255,255,0.05);
  }
  * { box-sizing: border-box; margin: 0; padding: 0; }
  html, body { width: 1200px; height: 852px; overflow: hidden; }
  body {
    background: var(--backdrop);
    display: flex;
    align-items: center;
    justify-content: center;
    gap: 60px;
    font-family: "Open Sans", Arial, sans-serif;
  }
  .card {
    position: relative;
    width: 480px;
    height: 280px;
    border-radius: 22px;
    overflow: hidden;
    background: var(--card-black);
    box-shadow: 0 10px 24px rgba(0,0,0,0.25);
  }
  .card-front {
    background: linear-gradient(120deg, var(--card-black) 0%, var(--card-black-soft) 42%, var(--card-black) 60%, #111 100%);
  }
  .ghost-ring {
    position: absolute;
    border-radius: 50%;
    border: 26px solid var(--ghost-ring);
  }
  .card-front .ghost-ring { width: 260px; height: 260px; right: -80px; top: -50px; }
  .card-back .ghost-ring { width: 240px; height: 240px; right: -70px; top: -70px; }

  .front-brand {
    position: absolute;
    left: 0; right: 0; top: 78px;
    display: flex;
    flex-direction: column;
    align-items: center;
    gap: 14px;
  }
  .brand-dot {
    width: 64px; height: 64px;
    border-radius: 50%;
    background: var(--brand-orange);
  }
  .brand-name {
    font-family: "Montserrat", Arial, sans-serif;
    font-weight: 800;
    color: var(--text-white);
    font-size: 40px;
    letter-spacing: -0.5px;
    line-height: 1;
  }

  .back-shape { position: absolute; inset: 0; }
  .back-brand {
    position: absolute;
    left: 26px; top: 22px;
    height: 236px;
    display: flex;
    flex-direction: column;
    align-items: center;
    justify-content: center;
    gap: 14px;
    width: 120px;
  }
  .back-brand .brand-dot {
    width: 52px; height: 52px;
    background: var(--card-black);
  }
  .back-brand .brand-name {
    writing-mode: vertical-rl;
    color: var(--card-black);
    font-size: 28px;
    line-height: 1.05;
  }
  .contact {
    position: absolute;
    left: 232px;
    top: 84px;
    color: var(--text-white);
  }
  .contact-name {
    font-family: "Open Sans", Arial, sans-serif;
    font-weight: 700;
    color: var(--brand-orange);
    font-size: 17px;
    line-height: 1.2;
  }
  .contact-role {
    font-size: 11px;
    color: var(--text-muted);
    margin: 2px 0 0 10px;
  }
  .contact-list {
    list-style: none;
    margin-top: 34px;
    display: flex;
    flex-direction: column;
    gap: 5px;
  }
  .contact-list li {
    display: flex;
    align-items: center;
    gap: 9px;
    font-size: 11.5px;
    line-height: 1.2;
  }
  .contact-list svg { width: 11px; height: 11px; flex: none; fill: var(--brand-orange); }
  .accent { color: var(--brand-orange); }
</style>
</head>
<body>

  <section class="card card-front" aria-label="Card front">
    <div class="ghost-ring"></div>
    <div class="front-brand">
      <div class="brand-dot"></div>
      <div class="brand-name">Kestrel Homes</div>
    </div>
  </section>

  <section class="card card-back" aria-label="Card back">
    <div class="ghost-ring"></div>
    <svg class="back-shape" viewBox="0 0 480 280" preserveAspectRatio="none">
      <path d="M0 0 H150 Q235 130 175 280 H0 Z" fill="var(--brand-orange)"/>
      <path d="M140 0 Q226 120 176 232" fill="none" stroke="var(--card-black)" stroke-width="5"/>
      <path d="M156 0 Q246 118 196 236" fill="none" stroke="var(--card-black)" stroke-width="3"/>
    </svg>

    <div class="back-brand">
      <div class="brand-dot"></div>
      <div class="brand-name">Kestrel Homes</div>
    </div>

    <div class="contact">
      <div class="contact-name">Harriet Colvane</div>
      <div class="contact-role">Owner / Proprietor</div>
      <ul class="contact-list">
        <li>
          <svg viewBox="0 0 12 12"><rect x="2.5" y="0.5" width="7" height="11" rx="1.5"/><rect x="4" y="2" width="4" height="6.5" fill="#0d0d0e"/></svg>
          0487309625
        </li>
        <li>
          <svg viewBox="0 0 12 12"><path d="M6 0.5a4 4 0 0 0-4 4c0 3 4 7 4 7s4-4 4-7a4 4 0 0 0-4-4z"/><circle cx="6" cy="4.5" r="1.5" fill="#0d0d0e"/></svg>
          PO Box 872, Tallowvale
        </li>
        <li>
          <svg viewBox="0 0 12 12"><rect x="0.5" y="2" width="11" height="8" rx="1"/><path d="M1 2.8 L6 6.6 L11 2.8" fill="none" stroke="#0d0d0e" stroke-width="1"/></svg>
          <span>harrietcolvane@<span class="accent">kestrelhomes</span>.example</span>
        </li>
      </ul>
    </div>
  </section>

</body>
</html>
```